Redesign for a start up airline technology. The website is quelbrion.com.

I need a PowerPoint template that complements our website. I can provide our current template as a starting point.

```html
<!DOCTYPE html>
<html lang="en">
<head>
<meta charset="utf-8">
<title>Quelbrion — Presentation Template</title>
<link rel="stylesheet" href="https://fonts.googleapis.com/css2?family=Montserrat:wght@400;500;600;700;800&family=Roboto+Slab:wght@600;700;800&display=swap">
<style>
:root{
  --paper:#e9eaec;
  --navy:#0c1220;
  --navy-2:#111a2c;
  --panel:#0a0f1b;
  --cyan:#1ec4f1;
  --blue:#0b63c4;
  --green:#8fd629;
  --green-2:#5fbf2a;
  --white:#ffffff;
  --muted:#b9c2d0;
  --dim:#7f8a9c;
}
*{box-sizing:border-box;margin:0;padding:0}
html,body{width:1083px;height:1200px;overflow:hidden;background:var(--paper)}
body{position:relative;font-family:"Montserrat",Arial,sans-serif;color:var(--white)}
.slide{position:absolute;width:315px;height:177px;background:var(--navy);overflow:hidden;box-shadow:0 3px 8px rgba(0,0,0,.28)}
.c1{left:56px}.c2{left:384px}.c3{left:712px}
.r1{top:44px}.r2{top:231px}.r3{top:419px}.r4{top:607px}.r5{top:797px}.r6{top:987px}
.abs{position:absolute}
.photo{position:absolute}
.h{position:absolute;left:11px;top:9px;font-family:"Roboto Slab",Georgia,serif;font-weight:700;font-size:10.5px;line-height:1.15;color:var(--white)}
.h::after{content:"";display:block;width:12px;height:1.5px;background:var(--blue);margin-top:4px}
.brand-sm{position:absolute;right:8px;top:8px;font-weight:700;font-size:5.6px;color:var(--cyan);letter-spacing:.2px}
.foot-site{position:absolute;left:10px;bottom:7px;font-size:3px;letter-spacing:1px;color:var(--cyan);display:flex;align-items:center;gap:3px}
.foot-site::after{content:"";width:40px;height:.4px;background:var(--green-2)}
.foot-copy{position:absolute;right:11px;bottom:7px;font-size:1.8px;color:var(--dim)}
.foot-num{position:absolute;right:4px;bottom:6px;width:5px;height:4px;background:var(--green);font-size:2.4px;color:var(--navy);text-align:center;line-height:4px;font-weight:700}
.micro{font-size:2.6px;line-height:1.35;color:var(--muted)}
.t-green{color:var(--green)}.t-cyan{color:var(--cyan)}
.lbl{font-weight:700;font-size:4.4px}

/* slide 1 */
.s1 .photo{left:70px;top:0;width:245px;height:177px;background:radial-gradient(ellipse at 55% 40%,#8a5a34 0%,#3b2e27 35%,#141414 75%)}
.s1 .fade{position:absolute;left:0;top:0;width:200px;height:177px;background:linear-gradient(90deg,#0d0d0f 40%,rgba(13,13,15,0))}
.s1 .sq{position:absolute;left:8px;top:7px;width:8px;height:8px;background:var(--green)}
.brand-lg{position:absolute;font-weight:700;color:var(--cyan)}
.s1 .brand-lg{left:20px;top:27px;font-size:12px}
.s1 .kick{left:20px;top:70px;font-size:8.5px;font-weight:400}
.s1 .big{left:20px;top:80px;font-size:18px;font-weight:800;color:var(--cyan)}
.s1 .mid{left:20px;top:99px;font-size:12.5px;font-weight:700;color:var(--green)}
.s1 .sub{left:20px;top:123px;font-size:6.6px;font-weight:600;color:var(--green)}
.s1 .lede{left:20px;top:132px;width:95px;font-size:3.7px;font-style:italic;color:var(--white);line-height:1.4}
.s1 .site{left:20px;top:158px;font-size:3.2px;letter-spacing:1.4px;display:flex;align-items:center;gap:3px}
.s1 .site::after{content:"";width:250px;height:.4px;background:var(--green-2)}

/* slide 2 */
.s2{background:#070b14}
.s2 .photo{left:110px;top:0;width:205px;height:177px;background:radial-gradient(ellipse at 55% 50%,#b9874a 0%,#2a5a78 30%,#0b2338 65%,#06101c 100%)}
.s2 .sq{position:absolute;left:8px;top:7px;width:8px;height:8px;background:var(--cyan)}
.s2 .brand-lg{left:23px;top:41px;font-size:12px}
.s2 .band{position:absolute;left:12px;top:91px;width:119px;height:29px;background:linear-gradient(90deg,var(--green-2),var(--green))}
.s2 .band::after{content:"";position:absolute;right:-2px;top:-2px;width:5px;height:5px;background:var(--cyan)}
.s2 .band p{position:absolute;left:7px;color:#0a1a10}
.s2 .band .a{top:4px;font-size:7px;color:var(--white)}
.s2 .band .b{top:14px;font-size:9px;font-weight:700;color:#0c2a4a}
.s2 .sub{left:19px;top:126px;font-size:6px;font-weight:600;color:var(--green)}
.s2 .lede{left:19px;top:134px;width:90px;font-size:3.6px;font-style:italic;line-height:1.4}
.s2 .site{left:19px;top:162px;font-size:3.2px;letter-spacing:1.4px;color:var(--cyan)}

/* slide 3 */
.s3{background:linear-gradient(135deg,#141b28,#0c111c)}
.s3 .panel{position:absolute;left:75px;top:29px;width:190px;height:119px;background:var(--panel)}
.s3 .agenda{position:absolute;left:29px;top:68px;width:84px;height:40px;background:linear-gradient(90deg,var(--blue),var(--cyan));font-family:"Roboto Slab",Georgia,serif;font-weight:700;font-size:14.5px;display:flex;align-items:center;justify-content:center}
.s3 .bar1{position:absolute;left:37px;top:63px;width:3px;height:8px;background:var(--green)}
.s3 .bar2{position:absolute;left:93px;top:105px;width:3px;height:8px;background:var(--green)}
.s3 .item{position:absolute;left:129px;width:115px}
.s3 .item .lbl{font-size:5px;color:var(--green)}
.s3 .item .lbl b{color:var(--cyan);font-weight:700}

/* slide 4 */
.s4 .photo{left:151px;top:0;width:164px;height:177px;background:radial-gradient(ellipse at 50% 35%,#2d6f9e 0%,#133a5c 40%,#0a1a2c 90%)}
.s4 .t1{left:21px;top:16px;font-family:"Roboto Slab",Georgia,serif;font-size:15px;font-weight:700}
.s4 .t2{left:21px;top:35px;background:var(--blue);padding:1px 3px;font-family:"Roboto Slab",Georgia,serif;font-size:11.5px;font-weight:700}
.s4 .p{left:20px;width:118px;font-size:3.8px;line-height:1.35;color:var(--muted)}

/* slide 5 */
.s5 .photo{left:0;top:0;width:315px;height:73px;background:linear-gradient(180deg,#6f8faa 0%,#3d5b77 55%,#1a2a3e 100%)}
.s5 .box{position:absolute;left:26px;top:42px;width:80px;height:100px;background:linear-gradient(180deg,var(--green-2),var(--green));padding:6px 7px}
.s5 .box h3{font-family:"Roboto Slab",Georgia,serif;font-size:11px;font-weight:700}
.s5 .box p{font-size:3.7px;line-height:1.3;margin-top:5px;color:var(--white)}
.bul{position:absolute;width:78px}
.bul .lbl{font-size:5px;color:var(--cyan);display:flex;align-items:center;gap:3px;margin-left:-7px}
.bul .lbl::before{content:"";width:4px;height:4px;border-radius:50%;background:var(--cyan)}

/* slide 6 */
.s6 .t{left:14px;top:16px;font-family:"Roboto Slab",Georgia,serif;font-size:12px;font-weight:700;line-height:1.15}
.s6 .t::after{content:"";display:block;width:12px;height:1.5px;background:var(--blue);margin-top:5px}
.s6 .photo{left:68px;top:0;width:112px;height:177px;background:radial-gradient(ellipse at 45% 40%,#7c5a85 0%,#2e3d64 35%,#0d1b30 85%)}
.s6 .p{left:14px;top:73px;width:50px;font-size:3.5px;line-height:1.35;color:var(--muted)}
.s6 .ic{position:absolute;left:168px;width:23px;height:23px;background:linear-gradient(180deg,var(--green),var(--green-2))}
.s6 .tx{position:absolute;left:201px;width:100px}
.s6 .tx .lbl{font-size:6.5px;color:var(--cyan);font-weight:800}

/* slide 7 */
.s7 .it{position:absolute;left:33px;width:115px}
.s7 .it .lbl{color:var(--cyan);font-size:4.8px}
.s7 .it .lbl b{color:var(--green);font-size:6px;margin-right:2px}
.s7 .it .micro{color:var(--white);padding-left:12px}
.s7 .panel{position:absolute;left:173px;top:39px;width:101px;height:105px;background:linear-gradient(90deg,var(--green-2),var(--green))}
.s7 .circ{position:absolute;left:167px;width:21px;height:21px;border-radius:50%;background:var(--cyan);border:2px solid #fff}
.s7 .pt{position:absolute;left:193px;width:78px}
.s7 .pt .lbl{font-size:6px}
.s7 .pt .micro{color:#e8f7d6}

/* slide 8 */
.s8 .cell{position:absolute;width:60px;text-align:center}
.s8 .sq{width:23px;height:23px;margin:0 auto 4px;border:1px solid #fff}
.s8 .sq.g{background:linear-gradient(180deg,var(--green),var(--green-2))}
.s8 .sq.c{background:linear-gradient(180deg,var(--cyan),#0a8fd0)}
.s8 .lbl{color:var(--green);font-size:5px}

/* slide 9 */
.s9 .ring{position:absolute;left:27px;top:50px;width:77px;height:77px;border-radius:50%;border:2.5px solid #d9dde3;box-shadow:inset 0 0 0 2px var(--green-2);background:var(--navy);display:flex;align-items:center;justify-content:center;font-weight:700;font-size:7.5px;color:var(--cyan)}
.s9 .ico{position:absolute;left:150px;width:24px;height:24px;border-radius:50%;background:radial-gradient(circle,var(--cyan),var(--blue));border:1px solid #fff}
.s9 .tx{position:absolute;left:182px;width:120px}
.s9 .tx .lbl{color:var(--green);font-size:5px;font-weight:600}

/* slide 10 */
.s10 .p{left:14px;top:32px;width:122px;font-size:3.7px;line-height:1.35;color:var(--muted)}
.s10 .leg{position:absolute;width:68px}
.s10 .leg .lbl{font-size:5px;display:flex;align-items:center;gap:3px}
.s10 .leg .lbl::before{content:"";width:4px;height:4px;border-radius:50%}
.s10 .leg.g .lbl::before{background:var(--green)}
.s10 .leg.c .lbl::before{background:var(--cyan)}

/* slide 11 */
.s11 .t{left:14px;top:10px;font-family:"Roboto Slab",Georgia,serif;font-weight:700;font-size:10.5px;line-height:1.3}
.s11 .t::after{content:"";display:block;width:17px;height:1.5px;background:var(--blue);margin-top:6px}
.s11 .photo{left:0;top:51px;width:210px;height:109px;background:linear-gradient(180deg,#8aa3bd 0%,#5d6f86 45%,#2a3444 100%)}
.s11 .box{position:absolute;left:26px;top:75px;width:58px;height:78px;background:linear-gradient(180deg,var(--green-2),var(--green));padding:5px}
.s11 .box h3{font-family:"Roboto Slab",Georgia,serif;font-size:8.5px;font-weight:700}
.s11 .box p{font-size:2.7px;line-height:1.3;margin-top:4px}
.s11 .p{left:217px;top:50px;width:89px;font-size:3.8px;line-height:1.3;color:var(--muted);text-align:justify}
.s11 .p span{display:block;margin-bottom:4px}

/* slide 12 */
.s12 .sw{position:absolute;width:40px;height:40px;border-radius:50%;display:flex;align-items:center;justify-content:center;font-size:17px;font-weight:700;color:#fff}
.s12 .g{background:var(--green)}.s12 .c{background:var(--cyan)}
.s12 .hub{position:absolute;left:142px;top:77px;width:32px;height:30px;border-radius:50%;background:var(--navy);border:1px solid #fff;display:flex;align-items:center;justify-content:center;font-size:4.4px;font-weight:700;color:var(--cyan)}
.s12 .cap{position:absolute;width:44px}
.s12 .cap .lbl{font-size:4.2px;font-style:normal;color:var(--green);font-weight:600}
.s12 .cap.c .lbl{color:var(--cyan)}
.s12 .cap .micro{font-size:2.1px;color:var(--white)}

/* slide 13 */
.s13 .t{left:0;top:25px;width:315px;text-align:center;font-family:"Roboto Slab",Georgia,serif;font-weight:700;font-size:10.5px}
.s13 .t::after{content:"";display:block;width:12px;height:1.5px;background:var(--blue);margin:3px auto 0}
.s13 .p{left:40px;width:235px;text-align:center;font-size:3.6px;color:var(--muted);line-height:1.35}
.s13 .pn{position:absolute;top:86px;height:57px;padding:6px}
.s13 .pn h3{font-family:"Roboto Slab",Georgia,serif;font-size:7.5px;font-weight:700}
.s13 .pn p{font-size:3.1px;line-height:1.3;margin-top:3px}
.s13 .photo{left:115px;top:86px;width:85px;height:57px;background:linear-gradient(180deg,#d9dee6 0%,#8e98a8 45%,#2c333f 100%)}

/* slide 14 */
.s14 .tx{position:absolute;width:80px;font-size:3.3px;line-height:1.3;color:var(--muted)}
.s14 .tx.l{text-align:right}
.s14 .tx b{display:block;font-family:"Roboto Slab",Georgia,serif;font-size:5px;color:var(--green);font-weight:700}

/* slide 15 */
.s15 .col{position:absolute;top:96px;width:44px;text-align:center}
.s15 .col .lbl{font-size:4.3px;color:var(--cyan);font-weight:600}
.s15 .col .micro{font-size:2.8px;color:var(--white);margin-top:3px}

/* slide 16 */
.s16 .photo{top:49px;width:63px;height:35px}
.s16 .ph1{left:27px;background:linear-gradient(180deg,#b9cbdc,#5a6e83 60%,#2b3440)}
.s16 .ph2{left:103px;background:linear-gradient(180deg,#c9d3de,#7b8795 60%,#333b47)}
.s16 .col{position:absolute;top:91px;width:64px}
.s16 .col .lbl{color:var(--green);font-size:6px;font-weight:700}
.s16 .col .micro{font-size:2.3px;color:var(--white);margin-top:2px}
.s16 .big{left:183px;top:53px;font-family:"Roboto Slab",Georgia,serif;font-weight:700;font-size:13.5px;line-height:1.17}
.s16 .box{position:absolute;left:178px;top:103px;width:110px;height:28px;background:linear-gradient(90deg,var(--green-2),var(--green));padding:5px 7px;font-size:3.8px;line-height:1.35;color:#10210b}

/* slide 17 */
.s17 .m{position:absolute;top:54px;width:46px;text-align:center}
.s17 .m .top{height:19px}
.s17 .m .top.g{background:linear-gradient(90deg,var(--green-2),var(--green))}
.s17 .m .top.b{background:linear-gradient(90deg,var(--blue),var(--cyan))}
.s17 .m .av{width:24px;height:24px;border-radius:50%;margin:-12px auto 0;border:1.5px solid #fff;background:radial-gradient(circle at 50% 40%,#d7d2cc,#8c8782)}
.s17 .m .lbl{color:var(--green);font-size:5.3px;margin-top:3px;font-weight:600}
.s17 .m .micro{font-size:2.3px;color:var(--white);margin-top:1px}

/* slide 18 */
.s18{background:linear-gradient(135deg,#0f1d3a,#0a1124 60%,#101a33)}
.s18 .photo{left:0;top:0;width:315px;height:177px;background:radial-gradient(ellipse at 35% 30%,rgba(50,80,140,.45),rgba(10,17,36,0) 60%)}
.s18 .brand-lg{left:44px;top:88px;font-size:17px}
.s18 .ty{left:168px;top:48px;font-size:19px;font-weight:700}
.s18 .ct{position:absolute;left:168px;display:flex;align-items:center;gap:4px}
.s18 .ct .sep{width:.6px;height:9px;background:#fff}
.s18 .ct p{font-size:4.3px;line-height:1.3}
</style>
</head>
<body>

<!-- Row 1 -->
<section class="slide s1 c1 r1">
  <div class="photo" role="img" aria-label="Propeller aircraft parked in a dimly lit hangar"></div>
  <div class="fade"></div>
  <div class="sq"></div>
  <p class="brand-lg">Quelbrion</p>
  <p class="abs kick">Presentation</p>
  <p class="abs big">Business</p>
  <p class="abs mid">Marketing</p>
  <p class="abs sub">Presentation</p>
  <p class="abs lede">Lorem ipsum dolor sit amet, consectetuer adipiscing elit, sed diam nonum</p>
  <p class="abs site">quelbrion.com</p>
</section>

<section class="slide s2 c2 r1">
  <div class="photo" role="img" aria-label="Wireframe airliner glowing on a blue-lit hangar floor"></div>
  <div class="sq"></div>
  <p class="brand-lg">Quelbrion</p>
  <div class="band"><p class="a">Presentation</p><p class="b">Business Marketing</p></div>
  <p class="abs sub">Presentation</p>
  <p class="abs lede">Lorem ipsum dolor sit amet, consectetuer adipiscing elit, sed diam nonum</p>
  <p class="abs site">quelbrion.com</p>
</section>

<section class="slide s3 c3 r1">
  <p class="brand-sm">Quelbrion</p>
  <div class="panel"></div>
  <div class="agenda">Agenda</div>
  <div class="bar1"></div><div class="bar2"></div>
  <div class="item" style="top:41px"><p class="lbl"><b>1.</b> Lorem ipsum</p><p class="micro">Lorem ipsum dolor sit amet, consectetuer adipiscing elit, sed diam nonummy nibh euismod tincid</p></div>
  <div class="item" style="top:68px"><p class="lbl"><b>2.</b> Lorem ipsum</p><p class="micro">Lorem ipsum dolor sit amet, consectetuer adipiscing elit, sed diam nonummy nibh euismod tincid</p></div>
  <div class="item" style="top:95px"><p class="lbl"><b>3.</b> Lorem ipsum</p><p class="micro">Lorem ipsum dolor sit amet, consectetuer adipiscing elit, sed diam nonummy nibh euismod tincid</p></div>
  <div class="item" style="top:120px"><p class="lbl"><b>4.</b> Lorem ipsum</p><p class="micro">Lorem ipsum dolor sit amet, consectetuer adipiscing elit, sed diam nonummy nibh euismod tincid</p></div>
  <p class="foot-site">quelbrion.com</p><p class="foot-copy">Copyright © 2024 Quelbrion. All rights reserved.</p><p class="foot-num">2</p>
</section>

<!-- Row 2 -->
<section class="slide s4 c1 r2">
  <div class="photo" role="img" aria-label="Hand holding a tablet with a small airplane hovering above it"></div>
  <p class="brand-sm">Quelbrion</p>
  <p class="abs t1">Subject</p>
  <p class="abs t2">Title</p>
  <p class="abs p" style="top:65px">Lorem ipsum dolor sit amet, consectetuer adipiscing elit, sed diam nonummynibh euismod tincidunt ut laoreet dolore magna aliquamerat volutpat. Ut wisi enimad minim veniam quis.</p>
  <p class="abs p" style="top:93px">nostrud exerci tation ullamcorper suscipit lobortis nisl ut aliquip ex ea commodo consequat. Duis autem vel eum iriure.</p>
  <svg class="abs" style="left:23px;top:108px" width="120" height="32" viewBox="0 0 120 32">
    <g fill="none" stroke-width="1.6">
      <circle cx="14" cy="13" r="10" stroke="#2a3346"/><circle cx="14" cy="13" r="10" stroke="#1ec4f1" stroke-dasharray="31.4 62.8" transform="rotate(-90 14 13)"/>
      <circle cx="46" cy="13" r="10" stroke="#2a3346"/><circle cx="46" cy="13" r="10" stroke="#8fd629" stroke-dasharray="47.1 62.8" transform="rotate(-90 46 13)"/>
      <circle cx="78" cy="13" r="10" stroke="#2a3346"/><circle cx="78" cy="13" r="10" stroke="#5fbf2a" stroke-dasharray="25.1 62.8" transform="rotate(-90 78 13)"/>
    </g>
    <g fill="#fff" font-family="Montserrat,sans-serif" font-size="4.6" font-weight="600" text-anchor="middle">
      <text x="14" y="14.6">50%</text><text x="46" y="14.6">75%</text><text x="78" y="14.6">40%</text>
    </g>
    <g fill="#9aa4b4" font-family="Montserrat,sans-serif" font-size="1.8" text-anchor="middle">
      <text x="14" y="28">Lorem ipsum dolor sit</text><text x="46" y="28">Lorem ipsum dolor sit</text><text x="78" y="28">Lorem ipsum dolor sit</text>
    </g>
  </svg>
  <p class="foot-site">quelbrion.com</p><p class="foot-copy">Copyright © 2024 Quelbrion. All rights reserved.</p><p class="foot-num">3</p>
</section>

<section class="slide s5 c2 r2">
  <div class="photo" role="img" aria-label="Airliner parked at an airport apron under a grey sky"></div>
  <p class="brand-sm">Quelbrion</p>
  <div class="box"><h3>Text Here</h3>
    <p>Lorem ipsum dolor sit amet, consectetuer adipiscing elit, sed diam nonummy nibh euismod tincidunt ut laoreet dolore magna aliquam erat volutpat.</p>
    <p>Ut wisi enim ad minim veniam, quis nostrud exerci tation ullamcorper suscipit lobortis nisl ut aliquip ex ea commodo conse</p></div>
  <div class="bul" style="left:128px;top:81px"><p class="lbl">Lorem ipsum</p><p class="micro">Lorem ipsum dolor sit amet, consectetuer adipiscing elit, sed diam nonummy nibh euismod tincidunt ut laoreet</p></div>
  <div class="bul" style="left:216px;top:81px"><p class="lbl">Lorem ipsum</p><p class="micro">Lorem ipsum dolor sit amet, consectetuer adipiscing elit, sed diam nonummy nibh euismod tincidunt ut laoreet</p></div>
  <div class="bul" style="left:128px;top:116px"><p class="lbl">Lorem ipsum</p><p class="micro">Lorem ipsum dolor sit amet, consectetuer adipiscing elit, sed diam nonummy nibh euismod tincidunt ut laoreet</p></div>
  <div class="bul" style="left:216px;top:116px"><p class="lbl">Lorem ipsum</p><p class="micro">Lorem ipsum dolor sit amet, consectetuer adipiscing elit, sed diam nonummy nibh euismod tincidunt ut laoreet</p></div>
  <p class="foot-site">quelbrion.com</p><p class="foot-copy">Copyright © 2024 Quelbrion. All rights reserved.</p><p class="foot-num">4</p>
</section>

<section class="slide s6 c3 r2">
  <div class="photo" role="img" aria-label="Airliner flying over a glowing city map at dusk"></div>
  <p class="brand-sm">Quelbrion</p>
  <p class="abs t">Text<br>Added<br>Here</p>
  <p class="abs p">Lorem ipsum dolor sit amet, consectetuer adipiscing elit, sed diam nonummy nibh euismod tincidunt ut laoreet dolore magna aliquam erat volutpat.<br><br>Ut wisi enim ad minim veniam, quis nostrud exerci tation ullamcorper suscipit lobortis nisl ut aliquip ex ea commodo</p>
  <div class="ic" style="top:30px"></div><div class="ic" style="top:76px"></div><div class="ic" style="top:123px"></div>
  <svg class="abs" style="left:168px;top:30px" width="23" height="116" viewBox="0 0 23 116" fill="#fff">
    <circle cx="8" cy="9" r="2.3"/><circle cx="15" cy="9" r="2.3"/><circle cx="11.5" cy="8" r="2.6"/><path d="M4 17a4 4 0 0 1 8 0zM11 17a4 4 0 0 1 8 0zM7 17a4.5 4.5 0 0 1 9 0z"/>
    <circle cx="8.5" cy="52" r="2.2"/><circle cx="14.5" cy="52" r="2.2"/><rect x="6.5" y="55" width="4" height="9" rx="1"/><rect x="12.5" y="55" width="4" height="9" rx="1"/>
    <path d="M11.5 108l-4-4a2.4 2.4 0 0 1 4-2.6 2.4 2.4 0 0 1 4 2.6z"/><path d="M4 107h4l4 3h7v2H4z"/>
  </svg>
  <div class="tx" style="top:31px"><p class="lbl">We Before Me</p><p class="micro">ipsum dolor sit amet, cons ectetuer adipiscing elit, sed diam nonummy nibh euismod tincidunt ut laoreet</p></div>
  <div class="tx" style="top:77px"><p class="lbl">We Are Good People</p><p class="micro">ipsum dolor sit amet, cons ectetuer adipiscing elit, sed diam nonummy nibh euismod tincidunt ut laoreet dolore magna aliquam erat volutpat.</p></div>
  <div class="tx" style="top:124px"><p class="lbl">We Work with Heart</p><p class="micro">ipsum dolor sit amet, cons ectetuer adipiscing elit, sed diam nonummy nibh euismod tincidunt</p></div>
  <p class="foot-site">quelbrion.com</p><p class="foot-copy">Copyright © 2024 Quelbrion. All rights reserved.</p><p class="foot-num">5</p>
</section>

<!-- Row 3 -->
<section class="slide s7 c1 r3">
  <p class="brand-sm">Quelbrion</p>
  <p class="h">Text Here</p>
  <div class="it" style="top:42px"><p class="lbl"><b>01.</b> Aliquam Erat Volutpat</p><p class="micro">Lorem ipsum dolor sit amet, consectetuer adipiscing elit, sed diam nonummy nibh euismod</p></div>
  <div class="it" style="top:70px"><p class="lbl"><b>02.</b> Consectetuer Adipiscing Elit</p><p class="micro">Lorem ipsum dolor sit amet, consectetuer adipiscing elit, sed diam nonummy nibh euismod tincidunt ut laoreet</p></div>
  <div class="it" style="top:99px"><p class="lbl"><b>03.</b> Duis Autem Vel Eum</p><p class="micro">Lorem ipsum dolor sit amet, consectetuer adipiscing elit, sed diam nonummy nibh euismod tincidunt.</p></div>
  <div class="it" style="top:126px"><p class="lbl"><b>04.</b> Aliquam Erat Volutpat</p><p class="micro">Lorem ipsum dolor sit amet, consectetuer adipiscing elit, sed diam nonummy nibh euismod tincidunt ut laoreet.</p></div>
  <div class="panel"></div>
  <div class="circ" style="top:49px"></div><div class="circ" style="top:81px"></div><div class="circ" style="top:114px"></div>
  <svg class="abs" style="left:167px;top:49px" width="21" height="86" viewBox="0 0 21 86" fill="none" stroke="#fff" stroke-width="1">
    <rect x="6" y="6" width="9" height="6" rx=".6"/><path d="M8 15h5M10.5 12v3"/>
    <path d="M7 42a3 3 0 0 1 1-5.5 3.5 3.5 0 0 1 6.5 0.5 2.6 2.6 0 0 1-.5 5z"/><path d="M10.5 42v3M8 45h5"/>
    <path d="M5 76l4-4 3 3 4-5"/><circle cx="5" cy="76" r="1" fill="#fff"/><circle cx="16" cy="70" r="1" fill="#fff"/>
  </svg>
  <div class="pt" style="top:49px"><p class="lbl">Lorem ipsum</p><p class="micro">ipsum dolor sit amet, cons ectetuer adipiscing elit, sed diam nonummy nibh euismod tincidunt ut laoreet</p></div>
  <div class="pt" style="top:81px"><p class="lbl">Lorem ipsum</p><p class="micro">ipsum dolor sit amet, cons ectetuer adipiscing elit, sed diam nonummy nibh euismod tincidunt ut laoreet</p></div>
  <div class="pt" style="top:115px"><p class="lbl">Lorem ipsum</p><p class="micro">ipsum dolor sit amet, cons ectetuer adipiscing elit, sed diam nonummy nibh euismod tincidunt</p></div>
  <p class="foot-site">quelbrion.com</p><p class="foot-copy">Copyright © 2024 Quelbrion. All rights reserved.</p><p class="foot-num">6</p>
</section>

<section class="slide s8 c2 r3">
  <p class="brand-sm">Quelbrion</p>
  <p class="h">Text Added Here</p>
  <div class="cell" style="left:42px;top:33px"><div class="sq g"></div><p class="lbl">Lorem ipsum</p><p class="micro">Lorem ipsum dolor sit amet, consectetuer adipiscing elit, sed diam nonummy nibh euismod tincidunt ut laoreet</p></div>
  <div class="cell" style="left:128px;top:33px"><div class="sq c"></div><p class="lbl">Lorem ipsum</p><p class="micro">Lorem ipsum dolor sit amet, consectetuer adipiscing elit, sed diam nonummy nibh euismod tincidunt ut laoreet</p></div>
  <div class="cell" style="left:213px;top:33px"><div class="sq g"></div><p class="lbl">Lorem ipsum</p><p class="micro">Lorem ipsum dolor sit amet, consectetuer adipiscing elit, sed diam nonummy nibh euismod tincidunt ut laoreet</p></div>
  <div class="cell" style="left:42px;top:93px"><div class="sq c"></div><p class="lbl">Lorem ipsum</p><p class="micro">Lorem ipsum dolor sit amet, consectetuer adipiscing elit, sed diam nonummy nibh euismod tincidunt ut laoreet</p></div>
  <div class="cell" style="left:128px;top:93px"><div class="sq g"></div><p class="lbl">Lorem ipsum</p><p class="micro">Lorem ipsum dolor sit amet, consectetuer adipiscing elit, sed diam nonummy nibh euismod tincidunt ut laoreet</p></div>
  <div class="cell" style="left:213px;top:93px"><div class="sq c"></div><p class="lbl">Lorem ipsum</p><p class="micro">Lorem ipsum dolor sit amet, consectetuer adipiscing elit, sed diam nonummy nibh euismod tincidunt ut laoreet</p></div>
  <svg class="abs" style="left:0;top:0" width="315" height="177" viewBox="0 0 315 177" fill="none" stroke="#fff" stroke-width=".8">
    <circle cx="69" cy="42" r="2.2"/><circle cx="75" cy="42" r="2.2"/><path d="M65 50a4 4 0 0 1 8 0M71 50a4 4 0 0 1 8 0"/>
    <circle cx="158" cy="44" r="5"/><path d="M155 44h6M158 41v6"/>
    <path d="M237 50h12M239 50v-4M243 50v-6M247 50v-8M237 47l5-5 3 2 4-5"/>
    <path d="M66 100l4 8 4-4 5 6M66 100v12h14"/>
    <circle cx="158" cy="106" r="5"/><path d="M158 103v6M156.5 104.5h3M156.5 107.5h3"/>
    <circle cx="243" cy="104" r="4.5"/><path d="M240 108l-1 5 4-2 4 2-1-5"/>
  </svg>
  <p class="foot-site">quelbrion.com</p><p class="foot-copy">Copyright © 2024 Quelbrion. All rights reserved.</p><p class="foot-num">7</p>
</section>

<section class="slide s9 c3 r3">
  <p class="brand-sm">Quelbrion</p>
  <p class="h">Text Added Here</p>
  <div class="ring">Quelbrion</div>
  <svg class="abs" style="left:0;top:0" width="315" height="177" viewBox="0 0 315 177" fill="none" stroke="#c9ced6" stroke-width=".6">
    <path d="M105 70l14-20h29"/><path d="M109 89h39"/><path d="M105 108l14 20h29"/>
  </svg>
  <div class="ico" style="top:38px"></div><div class="ico" style="top:77px"></div><div class="ico" style="top:116px"></div>
  <svg class="abs" style="left:150px;top:38px" width="24" height="102" viewBox="0 0 24 102" fill="none" stroke="#fff" stroke-width=".9">
    <circle cx="12" cy="12" r="6"/><circle cx="12" cy="12" r="3"/><path d="M12 12l6-6"/>
    <circle cx="12" cy="51" r="6"/><circle cx="12" cy="51" r="3"/><path d="M12 51l6-6"/>
    <circle cx="12" cy="90" r="6"/><circle cx="12" cy="90" r="3"/><path d="M12 90l6-6"/>
  </svg>
  <div class="tx" style="top:38px"><p class="lbl">Project name</p><p class="micro">Lorem ipsum dolor sit amet, nec an dictas equidem appellantur, ut has commune accommodare. Mea illum, iudus soleat idpro.</p></div>
  <div class="tx" style="top:78px"><p class="lbl">Project name</p><p class="micro">Lorem ipsum dolor sit amet, nec an dictas equidem appellantur, ut has commune accommodare. Mea illum, iudus soleat idpro.</p></div>
  <div class="tx" style="top:119px"><p class="lbl">Project name</p><p class="micro">Lorem ipsum dolor sit amet, nec an dictas equidem appellantur, ut has commune accommodare. Mea illum, iudus soleat idpro.</p></div>
  <p class="foot-site">quelbrion.com</p><p class="foot-copy">Copyright © 2024 Quelbrion. All rights reserved.</p><p class="foot-num">8</p>
</section>

<!-- Row 4 -->
<section class="slide s10 c1 r4">
  <p class="brand-sm">Quelbrion</p>
  <p class="h">Text Added Here</p>
  <p class="abs p">Lorem ipsum dolor sit amet, consectetuer adipiscing elit, sed diam nonummy nibh euismod tincidunt ut laoreet dolore magna aliquam erat volutpat. Ut wisi enim ad minim veniam, quis nostrud exerci tation ullamcorper suscipit lobortis nisl ut aliquip ex ea commodo consequat. Duis autem vel eum iriure dolor in hendrerit i</p>
  <svg class="abs" style="left:0;top:0" width="315" height="177" viewBox="0 0 315 177">
    <g font-family="Montserrat,sans-serif" font-size="5.4" fill="#fff" text-anchor="end">
      <text x="32" y="81">50%</text><text x="32" y="93">40%</text><text x="32" y="104">30%</text><text x="32" y="116">20%</text><text x="32" y="128">10%</text>
    </g>
    <path d="M37 75v68h60" stroke="#fff" stroke-width=".8" fill="none"/>
    <rect x="48" y="79" width="7.5" height="62" fill="#8fd629"/>
    <rect x="65" y="94" width="7.5" height="47" fill="#1ec4f1"/>
    <rect x="82" y="120" width="7.5" height="21" fill="#8fd629"/>
    <rect x="99" y="133" width="7.5" height="8" fill="#1ec4f1"/>
    <g font-family="Montserrat,sans-serif" font-size="5.4" fill="#fff" text-anchor="middle">
      <text x="52" y="152">1980</text><text x="69" y="152">1990</text><text x="86" y="152">2000</text><text x="103" y="152">2010</text>
    </g>
    <g fill="none" stroke-linecap="round" transform="rotate(-90 219 71)">
      <circle cx="219" cy="71" r="52" stroke="#8fd629" stroke-width="2.6" stroke-dasharray="222 327"/>
      <circle cx="219" cy="71" r="47" stroke="#1ec4f1" stroke-width="2.6" stroke-dasharray="200 296"/>
      <circle cx="219" cy="71" r="42" stroke="#1ec4f1" stroke-width="2.6" stroke-dasharray="150 264"/>
      <circle cx="219" cy="71" r="37" stroke="#8fd629" stroke-width="2.6" stroke-dasharray="140 233"/>
      <circle cx="219" cy="71" r="32" stroke="#1ec4f1" stroke-width="2.6" stroke-dasharray="120 201"/>
    </g>
    <g font-family="Montserrat,sans-serif" font-size="5" font-style="italic">
      <text x="173" y="50" fill="#8fd629">68%</text><text x="178" y="96" fill="#1ec4f1">45%</text>
      <text x="209" y="110" fill="#8fd629">35%</text><text x="229" y="96" fill="#1ec4f1">15%</text>
    </g>
    <text x="219" y="73" fill="#fff" font-family="Montserrat,sans-serif" font-size="7.5" font-weight="500" text-anchor="middle">Add Text</text>
  </svg>
  <div class="leg g" style="left:148px;top:136px"><p class="lbl">Lorem ipsum</p><p class="micro">Lorem ipsum dolor sit amet, consectetuer adipiscing elit, sed diam nonummy nibh euismod tincidunt ut laoreet</p></div>
  <div class="leg c" style="left:222px;top:136px"><p class="lbl">Lorem ipsum</p><p class="micro">Lorem ipsum dolor sit amet, consectetuer adipiscing elit, sed diam nonummy nibh euismod tincidunt ut laoreet</p></div>
  <p class="foot-site">quelbrion.com</p><p class="foot-copy">Copyright © 2024 Quelbrion. All rights reserved.</p><p class="foot-num">9</p>
</section>

<section class="slide s11 c2 r4">
  <p class="brand-sm">Quelbrion</p>
  <p class="abs t">Lorem Ipsum Dolor Sit<br>Ametkeeper.</p>
  <div class="photo" role="img" aria-label="Airliner on a wet apron at sunset with ground crew cones"></div>
  <div class="box"><h3>Text Here</h3>
    <p>Lorem ipsum dolor sit amet, consectetuer adipiscing elit, sed diam nonummy nibh euismod tincidunt ut laoreet dolore magna aliquam erat volutpat.</p>
    <p>Ut wisi enim ad minim veniam, quis nostrud exerci tation ullamcorper suscipit lobortis nisl ut aliquip ex ea commodo conse</p></div>
  <div class="abs p"><span>Lorem ipsum dolor sit amet, consectetuer adipiscing elit, sed diam nonummy nibh euismod tincidunt ut laoreet dolore magna aliquam erat volutpat.</span><span>Ut wisi enim ad minim veniam, quis nostrud exerci tation ullamcorper suscipit lobortis nisl ut aliquip ex ea commodo consequat. Duis autem vel eum iriure dolor in hendrerit in vulputate velit esse molestie consequat,</span><span>vel illum dolore eu feugiat nulla facilisis at vero eros et accumsan et iusto odio dignissim qui blandit praesent luptatum</span></div>
  <p class="foot-site">quelbrion.com</p><p class="foot-copy">Copyright © 2024 Quelbrion. All rights reserved.</p><p class="foot-num">10</p>
</section>

<section class="slide s12 c3 r4">
  <p class="brand-sm">Quelbrion</p>
  <p class="h">Text Added Here</p>
  <svg class="abs" style="left:0;top:0" width="315" height="177" viewBox="0 0 315 177" fill="none" stroke="#fff" stroke-width=".8" stroke-dasharray=".8 1.4">
    <path d="M158 38v125"/><path d="M100 92h116"/>
  </svg>
  <div class="sw g" style="left:114px;top:48px">S</div>
  <div class="sw c" style="left:162px;top:48px">W</div>
  <div class="sw c" style="left:114px;top:96px">O</div>
  <div class="sw g" style="left:162px;top:96px">T</div>
  <div class="hub">Quelbrion</div>
  <div class="cap" style="left:76px;top:38px"><p class="lbl">STRENGTHS</p><p class="micro">· Good location<br><br>· Very affordable prices<br><br>· Variety of activities<br><br>· Personal trainer</p></div>
  <div class="cap" style="left:206px;top:38px"><p class="lbl">WEAKNESSES</p><p class="micro">· Not many promotions during the year<br><br>· Small fitness training rooms<br><br>· Presence in social networks can be improved</p></div>
  <div class="cap c" style="left:76px;top:106px"><p class="lbl">OPPORTUNITIES</p><p class="micro">· Hiring more graphic designers and marketing members<br><br>· An app can be practical to track results, find information about nutrition and view workout statistics</p></div>
  <div class="cap" style="left:206px;top:106px"><p class="lbl">THREATS</p><p class="micro">· Others gyms have more super to workout and running clubs<br><br>· There are many free fitness app<br><br>· Principal competitors have nutricionist</p></div>
  <p class="foot-site">quelbrion.com</p><p class="foot-copy">Copyright © 2024 Quelbrion. All rights reserved.</p><p class="foot-num">11</p>
</section>

<!-- Row 5 -->
<section class="slide s13 c1 r5">
  <p class="brand-sm">Quelbrion</p>
  <p class="abs t">Text Added Here</p>
  <p class="abs p" style="top:48px">Lorem ipsum dolor sit amet, consectetuer adipiscing elit, sed diam nonummy nibh euismod tincidunt ut laoreet dolore magna aliquam erat volutpat.</p>
  <p class="abs p" style="top:63px">Ut wisi enim ad minim veniam, quis nostrud exerci tation ullamcorper suscipit lobortis nisl ut aliquip ex ea commodo consequat. Duis autem vel eum iriure dolor in hendrerit i</p>
  <div class="pn" style="left:40px;width:75px;background:var(--blue)"><h3>Text Here</h3><p>Lorem ipsum dolor sit amet, consectetuer adipiscing elit, sed diam nonummy nibh euismod tincidunt ut laoreet dolore magna aliquam erat volutpat.</p></div>
  <div class="photo" role="img" aria-label="Traveller and child silhouetted against airport terminal windows"></div>
  <div class="pn" style="left:200px;width:74px;background:var(--cyan)"><h3>Text Here</h3><p>Lorem ipsum dolor sit amet, consectetuer adipiscing elit, sed diam nonummy nibh euismod tincidunt ut laoreet dolore magna aliquam erat volutpat.</p></div>
  <p class="foot-site">quelbrion.com</p><p class="foot-copy">Copyright © 2024 Quelbrion. All rights reserved.</p><p class="foot-num">12</p>
</section>

<section class="slide s14 c2 r5">
  <p class="brand-sm">Quelbrion</p>
  <p class="h">Text Added Here</p>
  <svg class="abs" style="left:0;top:0" width="315" height="177" viewBox="0 0 315 177">
    <path d="M114 93A42 42 0 0 1 156 51V72A21 21 0 0 0 135 93Z" fill="#8fd629"/>
    <path d="M156 51A42 42 0 0 1 198 93H177A21 21 0 0 0 156 72Z" fill="#1ec4f1"/>
    <path d="M198 93A42 42 0 0 1 156 135V114A21 21 0 0 0 177 93Z" fill="#8fd629"/>
    <path d="M156 135A42 42 0 0 1 114 93H135A21 21 0 0 0 156 114Z" fill="#1ec4f1"/>
    <circle cx="156" cy="61" r="3.4" fill="#1ec4f1"/><circle cx="188" cy="93" r="3.4" fill="#8fd629"/>
    <circle cx="156" cy="125" r="3.4" fill="#8fd629"/><circle cx="124" cy="93" r="3.4" fill="#1ec4f1"/>
    <g stroke="#0c1220" stroke-width="1.2"><path d="M156 51v21M198 93h-21M156 135v-21M114 93h21"/></g>
    <g fill="none" stroke="#0c1220" stroke-width=".8">
      <circle cx="134" cy="71" r="4"/><circle cx="134" cy="71" r="1.6"/>
      <path d="M174 74l6-6M176 68h4v4"/>
      <circle cx="178" cy="115" r="4"/><circle cx="178" cy="115" r="1.6"/>
      <rect x="131" y="112" width="6" height="6" rx="1"/>
    </g>
    <text x="156" y="95" fill="#1ec4f1" font-family="Montserrat,sans-serif" font-size="5" font-weight="700" text-anchor="middle">Quelbrion</text>
  </svg>
  <div class="tx l" style="left:32px;top:52px"><b>Text Here</b>Lorem ipsum dolor sit amet, consectetuer adipiscing elit, sed diammy nibh euismod tincidunt ut laoreet dolore</div>
  <div class="tx" style="left:209px;top:52px"><b>Text Here</b>Lorem ipsum dolor sit amet, consectetuer adipiscing elit, sed diammy nibh euismod tincidunt ut laoreet dolore</div>
  <div class="tx l" style="left:32px;top:113px"><b>Text Here</b>Lorem ipsum dolor sit amet, consectetuer adipiscing elit, sed diammy nibh euismod tincidunt ut laoreet dolore</div>
  <div class="tx" style="left:209px;top:113px"><b>Text Here</b>Lorem ipsum dolor sit amet, consectetuer adipiscing elit, sed diammy nibh euismod tincidunt ut laoreet dolore</div>
  <p class="foot-site">quelbrion.com</p><p class="foot-copy">Copyright © 2024 Quelbrion. All rights reserved.</p><p class="foot-num">13</p>
</section>

<section class="slide s15 c3 r5">
  <p class="brand-sm">Quelbrion</p>
  <p class="h">Text Added Here</p>
  <svg class="abs" style="left:0;top:0" width="315" height="177" viewBox="0 0 315 177">
    <polygon points="38,58 81,58 91,72 81,86 38,86 48,72" fill="#8fd629"/>
    <polygon points="84,58 127,58 137,72 127,86 84,86 94,72" fill="#1ec4f1"/>
    <polygon points="130,58 173,58 183,72 173,86 130,86 140,72" fill="#8fd629"/>
    <polygon points="176,58 219,58 229,72 219,86 176,86 186,72" fill="#1ec4f1"/>
    <polygon points="222,58 265,58 275,72 265,86 222,86 232,72" fill="#8fd629"/>
    <g fill="#fff" font-family="Montserrat,sans-serif" font-size="5" font-weight="600" text-anchor="middle">
      <text x="65" y="74">STEP 01</text><text x="111" y="74">STEP 02</text><text x="157" y="74">STEP 03</text><text x="203" y="74">STEP 04</text><text x="249" y="74">STEP 05</text>
    </g>
  </svg>
  <div class="col" style="left:41px"><p class="lbl">Project name</p><p class="micro">Lorem Ipsum is simply dummy unknown printer took a galley of type and scrambled it to make.</p></div>
  <div class="col" style="left:89px"><p class="lbl">Project name</p><p class="micro">Lorem Ipsum is simply dummy unknown printer took a galley of type and scrambled it to make.</p></div>
  <div class="col" style="left:135px"><p class="lbl">Project name</p><p class="micro">Lorem Ipsum is simply dummy unknown printer took a galley of type and scrambled it to make.</p></div>
  <div class="col" style="left:181px"><p class="lbl">Project name</p><p class="micro">Lorem Ipsum is simply dummy unknown printer took a galley of type and scrambled it to make.</p></div>
  <div class="col" style="left:227px"><p class="lbl">Project name</p><p class="micro">Lorem Ipsum is simply dummy unknown printer took a galley of type and scrambled it to make.</p></div>
  <p class="foot-site">quelbrion.com</p><p class="foot-copy">Copyright © 2024 Quelbrion. All rights reserved.</p><p class="foot-num">14</p>
</section>

<!-- Row 6 -->
<section class="slide s16 c1 r6">
  <p class="brand-sm">Quelbrion</p>
  <p class="h">Text Added Here</p>
  <div class="photo ph1" role="img" aria-label="Traveller with suitcase by airport terminal windows"></div>
  <div class="photo ph2" role="img" aria-label="Passenger seated in a bright departure lounge"></div>
  <div class="col" style="left:27px"><p class="lbl">Text Here</p><p class="micro">Lorem ipsum dolor sit amet, consectetuer adipiscing elit, sed diam nonummy nibh euismod tincidunt ut laoreet dolore magna aliquam erat volutpat.<br><br>Lorem ipsum dolor sit amet, consectetuer adipiscing elit, sed diam nonummy nibh euismod tincidunt ut laoreet dolore magna aliquam erat volutpat.</p></div>
  <div class="col" style="left:103px"><p class="lbl">Text Here</p><p class="micro">Lorem ipsum dolor sit amet, consectetuer adipiscing elit, sed diam nonummy nibh euismod tincidunt ut laoreet dolore magna aliquam erat volutpat.<br><br>Lorem ipsum dolor sit amet, consectetuer adipiscing elit, sed diam nonummy nibh euismod tincidunt ut laoreet dolore magna aliquam erat volutpat.</p></div>
  <p class="abs big">Lorem Ipsum<br>Dolor Sit<br>Ametkeeper.</p>
  <div class="box">Lorem ipsum dolor sit amet, consectetuer adipiscing elit, sed diam euismod tincidunt ut laoreet dolore magna aliquam.</div>
  <p class="foot-site">quelbrion.com</p><p class="foot-copy">Copyright © 2024 Quelbrion. All rights reserved.</p><p class="foot-num">15</p>
</section>

<section class="slide s17 c2 r6">
  <p class="brand-sm">Quelbrion</p>
  <p class="h">Our Team</p>
  <div class="m" style="left:28px"><div class="top g"></div><div class="av" role="img" aria-label="Team member portrait"></div><p class="lbl">DANIEL REYES</p><p class="micro">ipsum dolor sit amet, cons ectetuer adipiscing elit, sed diam nonummy nibh euismod tincidunt<br><br>ut laoreet dolore magna aliquam erat volutpat. Ut wisi enim ad minim veniam, quis nostrud</p></div>
  <div class="m" style="left:97px"><div class="top b"></div><div class="av" role="img" aria-label="Team member portrait"></div><p class="lbl">NORA VANCE</p><p class="micro">ipsum dolor sit amet, cons ectetuer adipiscing elit, sed diam nonummy nibh euismod tincidunt<br><br>ut laoreet dolore magna aliquam erat volutpat. Ut wisi enim ad minim veniam, quis nostrud</p></div>
  <div class="m" style="left:167px"><div class="top g"></div><div class="av" role="img" aria-label="Team member portrait"></div><p class="lbl">DANIEL REYES</p><p class="micro">ipsum dolor sit amet, cons ectetuer adipiscing elit, sed diam nonummy nibh euismod tincidunt<br><br>ut laoreet dolore magna aliquam erat volutpat. Ut wisi enim ad minim veniam, quis nostrud</p></div>
  <div class="m" style="left:239px"><div class="top b"></div><div class="av" role="img" aria-label="Team member portrait"></div><p class="lbl">NORA VANCE</p><p class="micro">ipsum dolor sit amet, cons ectetuer adipiscing elit, sed diam nonummy nibh euismod tincidunt<br><br>ut laoreet dolore magna aliquam erat volutpat. Ut wisi enim ad minim veniam, quis nostrud</p></div>
  <p class="foot-site">quelbrion.com</p><p class="foot-copy">Copyright © 2024 Quelbrion. All rights reserved.</p><p class="foot-num">16</p>
</section>

<section class="slide s18 c3 r6">
  <div class="photo" role="img" aria-label="Faint airliner over a blue data backdrop"></div>
  <p class="brand-lg">Quelbrion</p>
  <p class="abs ty">Thank You</p>
  <div class="ct" style="top:84px">
    <svg width="7" height="8" viewBox="0 0 7 8"><path d="M1.5 .5l1.5 1.6-.8 1.1a4 4 0 0 0 1.8 2l1-.8 1.6 1.5-1 1.4C3.6 7 .4 3.9.2 1.5z" fill="#1ec4f1"/></svg>
    <span class="sep"></span><p>+18 5550 1204 3391<br>+18 5550 1204 3391</p></div>
  <div class="ct" style="top:101px">
    <svg width="7" height="8" viewBox="0 0 7 8"><path d="M.5 .5l6 3-2.6.8L2.8 7z" fill="#1ec4f1"/></svg>
    <span class="sep"></span><p>www.quelbrion.com<br>hello@quelbrion.com</p></div>
  <div class="ct" style="top:118px">
    <svg width="7" height="8" viewBox="0 0 7 8"><path d="M3.5 .6L.3 3.6h1v3.8h1.8V5.2h.8v2.2h1.8V3.6h1z" fill="#1ec4f1"/></svg>
    <span class="sep"></span><p>1234 Street name, town/city,<br>state/country, post/zip 012345.</p></div>
</section>

</body>
</html>
```